Summit Mindworks Business Card Design + Letterhead

I require a new business card and letterhead for my consulting business. I am a psychologist working predominantly in sport psychology and organisational psychology. I consult to elite athletes and corporates.
I provide counselling services, workshops, assessments, and group sessions.
I'd like to use the colours in the logo.
My current card and letterhead is predominantly white - which I do like, but I'm up to try something different as well!
The letterhead doesn't need to have my name or title on it - but it can
The company is about success, achievement and reaching potential.
My website is at www.crestmw.com.au
I have changed some of my contact details, so I definitely need a new card and I would like this project to go ahead.
Thank you for putting the time into my design - I'm really excited about a new card and appreciate your contribution.
*IMPORTANT: The Fax Number Should be: 07 46 81 53 29
Target Market(s)
Elite athletes and teams
Corporate clients
Industry/Entity Type
Business
Contact Information for Business Card
Dr Maribel Osgood
Director (this is optional - I don't have to have this on there)
Level 1, 248 Harlow St
Kestrel Bay KB 6021
M: 0419 356 214
F: 07 46 318 592
E: mo@crestmw.com.au
W: www.crestmw.com.au
Requirements
Must have
- Logo - I have one with a white background and one with blue - don't mind which one is used. Currently I have the white logo on letterhead and cards.
I would like to have the catchphrase of the company
... Rise to your summit
on the card somewhere.
Nice to have
- On my current card I have a few lines on the back to write appointment times for clients - however this isn't essential
I also have some of the key services provided:
- Performance Enhancement
- Assessment & Reports
- Individual & Group Counselling
- Executive coaching & Motivation
- Seminars & Workshops
I have a QR file - don't have it on my current card, but thinking it could go on the business card (probably not letterhead?). For some reason I can only load one file, so can send it through if it's needed.

```html
<!DOCTYPE html>
<html lang="en">
<head>
<meta charset="utf-8">
<title>Summit Mindworks – Stationery</title>
<link href="https://fonts.googleapis.com/css2?family=Questrial&display=swap" rel="stylesheet">
<style>
  :root{
    --navy:#1f2c7c;
    --sky:#1ba3e3;
    --sun:#f2c21b;
    --band:#e2e6ea;
    --paper:#ffffff;
    --stage:#e9e7e5;
    --ink:#2a2f4a;
  }
  *{margin:0;padding:0;box-sizing:border-box}
  html,body{width:1200px;height:843px;overflow:hidden}
  body{background:var(--stage);font-family:"Questrial",sans-serif;color:var(--ink);position:relative}

  .sheet{position:absolute;background:var(--paper);box-shadow:0 2px 6px rgba(0,0,0,.12);overflow:hidden}

  .brand{position:absolute;display:flex;align-items:center;gap:8px}
  .brand-dot{width:14px;height:14px;border-radius:50%;background:var(--sun);flex:none}
  .brand-name{color:var(--navy);font-size:20px;letter-spacing:.5px;white-space:nowrap}
  .brand--light .brand-name{color:#fff}

  .tagline{position:absolute;color:var(--sky);font-size:11px;letter-spacing:.8px;text-transform:uppercase;white-space:nowrap}
  .rule{position:absolute;height:1.5px;background:var(--sky)}

  /* letterhead */
  .letterhead{left:620px;top:40px;width:540px;height:764px}
  .letterhead .brand{left:40px;top:48px}
  .letterhead .rule{left:40px;right:40px;top:76px}
  .letterhead .tagline{right:40px;top:58px}
  .letterhead-footer{position:absolute;left:0;right:0;bottom:0;height:90px;background:var(--band);
    display:flex;align-items:flex-end;justify-content:center;padding-bottom:22px;font-size:8.6px;color:var(--navy);white-space:nowrap}
  .letterhead-footer b{color:var(--sky);font-weight:normal}
  .letterhead-footer .sep{margin:0 5px;color:var(--navy)}

  /* business card front */
  .card{width:480px;height:274px}
  .card-front{left:60px;top:110px}
  .card-front .brand{left:28px;top:56px}
  .card-front .rule{left:28px;right:26px;top:86px}
  .card-front .tagline{right:26px;top:68px;font-size:12px}
  .card-details{position:absolute;right:26px;top:94px;text-align:right;line-height:1.35}
  .card-details .web{font-size:10px;color:var(--navy)}
  .card-details .person{margin-top:14px;font-size:14px;color:var(--navy);letter-spacing:.5px;text-transform:uppercase}
  .card-details .role{font-size:9.5px;color:var(--ink)}
  .card-details .contact{font-size:10px;color:var(--navy)}
  .card-details .contact--first{margin-top:12px}
  .card-details .contact b{font-weight:normal;color:var(--navy)}
  .card-band{position:absolute;left:0;right:0;bottom:0;height:70px;background:var(--band);
    padding:22px 28px;font-size:10px;line-height:1.4;color:var(--navy)}

  /* business card back */
  .card-back{left:60px;top:444px;display:flex}
  .services-panel{position:relative;width:210px;height:100%;background:var(--navy);color:#fff;padding:0 18px}
  .services-panel .brand{left:18px;top:50px}
  .services-panel .brand-name{font-size:17px}
  .services{position:absolute;left:18px;top:130px;list-style:none;font-size:10.5px;line-height:1.55}
  .services li::before{content:"•";margin-right:6px}
  .appointments{flex:1;padding:26px 28px 0 34px}
  .appointments h2{font-weight:normal;font-size:12px;letter-spacing:1px;color:var(--navy);text-transform:uppercase;margin-bottom:12px}
  .appointment-row{display:flex;align-items:flex-end;gap:6px;font-size:10px;color:var(--navy);height:33px}
  .appointment-row .line{border-bottom:1px solid var(--navy);height:1px;flex:none}
  .appointment-row .slot{width:18px}
  .appointment-row .with{width:80px}
</style>
</head>
<body>

<section class="sheet letterhead" aria-label="Letterhead">
  <div class="brand"><span class="brand-dot"></span><span class="brand-name">Summit Mindworks</span></div>
  <p class="tagline">Rise to your summit</p>
  <div class="rule"></div>
  <footer class="letterhead-footer">
    248 Harlow St., Kestrel Bay KB 6021<span class="sep">•</span><b>Fax:</b>&nbsp;07 46 318 592<span class="sep">•</span><b>Mob:</b>&nbsp;0419 356 214<span class="sep">•</span><b>Email:</b>&nbsp;mo@crestmw.com.au<span class="sep">•</span>www.crestmw.com.au
  </footer>
</section>

<section class="sheet card card-front" aria-label="Business card front">
  <div class="brand"><span class="brand-dot"></span><span class="brand-name">Summit Mindworks</span></div>
  <p class="tagline">Rise to your summit</p>
  <div class="rule"></div>
  <div class="card-details">
    <p class="web">www.crestmw.com.au</p>
    <p class="person">Dr Maribel Osgood</p>
    <p class="role">Director</p>
    <p class="contact contact--first"><b>Mob:</b> 0419 356 214</p>
    <p class="contact"><b>Email:</b> mo@crestmw.com.au</p>
  </div>
  <div class="card-band">
    248 Harlow St., Kestrel Bay KB 6021<br>
    Fax: 07 46 318 592
  </div>
</section>

<section class="sheet card card-back" aria-label="Business card back">
  <div class="services-panel">
    <div class="brand brand--light"><span class="brand-dot"></span><span class="brand-name">Summit Mindworks</span></div>
    <ul class="services">
      <li>Performance Enhancement</li>
      <li>Assessment &amp; Reports</li>
      <li>Individual &amp; Group Counselling</li>
      <li>Executive coaching &amp; Motivation</li>
      <li>Seminars &amp; Workshops</li>
    </ul>
  </div>
  <div class="appointments">
    <h2>Your appointments</h2>
    <div class="appointment-row">1.<span class="line slot"></span>am/pm<span class="line with"></span><span>__/__/__</span></div>
    <div class="appointment-row">2.<span class="line slot"></span>am/pm<span class="line with"></span><span>__/__/__</span></div>
    <div class="appointment-row">3.<span class="line slot"></span>am/pm<span class="line with"></span><span>__/__/__</span></div>
    <div class="appointment-row">4.<span class="line slot"></span>am/pm<span class="line with"></span><span>__/__/__</span></div>
    <div class="appointment-row">5.<span class="line slot"></span>am/pm<span class="line with"></span><span>__/__/__</span></div>
    <div class="appointment-row">6.<span class="line slot"></span>am/pm<span class="line with"></span><span>__/__/__</span></div>
  </div>
</section>

</body>
</html>
```